Bath Salt Packaging

Hello! We are Dr Velmo Organics, a company providing the best and most nutritious food and health-care products for the health conscious around the world!
We are currently in the process of releasing a few new products, one of which is Himalayan Bath Salt Crystals. It is an ancient, pure salt which has been protected from environmental toxins and pollution under the Himalayan mountains for more than 250 million years!
Our salt is 100% pure and unrefined, still containing the original mineral composition of the ancient life-giving ocean that supported our early ancestors. There are over 60 trace minerals in this salt, the majority of which exist in colloidal forms, meaning they are highly bioavailable and quickly ionized when added to water.
So, we need packaging designed for our four salt packets; a 300mL jar, a 150mL jar, a 10g sachet and a box which will house the sachets. I have attached the label content, measurements and a little extra instruction/information.
We want a natural, eco-friendly feel for the packaging. Thanks!
ps. please use the 3rd of the Logo's (TM, 'Organics' under leaf)

```html
<!DOCTYPE html>
<html lang="en">
<head>
<meta charset="utf-8">
<title>Himalayan Bath Salt Crystals – Jar Label</title>
<link rel="stylesheet" href="https://fonts.googleapis.com/css2?family=Open+Sans:wght@400;700&family=Oswald:wght@600&family=Kaushan+Script&display=swap">
<style>
  :root {
    --page-bg: #f4f3f1;
    --label-bg: #ffffff;
    --ink-dark: #2f3a33;
    --script-green: #1f4a33;
    --leaf-green: #5aa829;
    --badge-green: #58b12f;
    --salt-pink: #f2b7a3;
    --salt-light: #fbe4da;
    --sack-brown: #a88663;
    --text-grey: #333333;
  }
  * { margin: 0; padding: 0; box-sizing: border-box; }
  html, body { width: 1200px; height: 961px; overflow: hidden; }
  body {
    background: var(--page-bg);
    display: flex;
    align-items: center;
    justify-content: center;
    font-family: "Open Sans", sans-serif;
  }
  .jar-label {
    position: relative;
    width: 520px;
    height: 890px;
    background: var(--label-bg);
    box-shadow: 0 2px 10px rgba(0,0,0,0.08);
  }
  .brand-name {
    position: absolute;
    top: 92px;
    left: 0;
    width: 100%;
    text-align: center;
    font-family: "Open Sans", sans-serif;
    font-weight: 400;
    font-size: 34px;
    color: var(--ink-dark);
  }
  .brand-name .tm { font-size: 14px; vertical-align: super; }
  .brand-dot {
    display: inline-block;
    width: 12px; height: 12px;
    border-radius: 50%;
    background: var(--leaf-green);
    margin-left: 8px;
    vertical-align: middle;
  }
  .product-title {
    position: absolute;
    top: 238px;
    left: 0;
    width: 100%;
    text-align: center;
    font-family: "Kaushan Script", cursive;
    font-size: 72px;
    line-height: 1;
    color: var(--script-green);
  }
  .product-subtitle {
    position: absolute;
    top: 340px;
    left: 0;
    width: 100%;
    text-align: center;
    font-family: "Oswald", sans-serif;
    font-weight: 600;
    font-size: 48px;
    line-height: 1;
    letter-spacing: -0.5px;
    color: var(--leaf-green);
  }
  .salt-photo {
    position: absolute;
    top: 460px;
    left: 80px;
    width: 420px;
    height: 300px;
    border-radius: 40% 45% 30% 35%;
    background: radial-gradient(ellipse at 35% 30%, var(--sack-brown) 0%, rgba(168,134,99,0.6) 28%, transparent 45%),
                radial-gradient(ellipse at 62% 62%, var(--salt-pink) 0%, var(--salt-light) 45%, transparent 72%);
  }
  .quality-badge {
    position: absolute;
    top: 567px;
    left: 43px;
    width: 250px;
    height: 250px;
  }
  .volume {
    position: absolute;
    top: 832px;
    left: 0;
    width: 100%;
    text-align: center;
    font-size: 22px;
    color: var(--text-grey);
  }
  .volume strong { font-weight: 700; }
</style>
</head>
<body>
  <main class="jar-label">
    <div class="brand-name">Dr Velmo Organics<span class="tm">™</span><span class="brand-dot"></span></div>

    <h1 class="product-title">Himalayan</h1>
    <h2 class="product-subtitle">BATH SALT CRYSTALS</h2>

    <div class="salt-photo" role="img" aria-label="Photo of a burlap sack spilling pink Himalayan salt crystals"></div>

    <svg class="quality-badge" viewBox="0 0 250 250" aria-label="Organic, Ecofriendly, Fair trading, Healthy, Sustainable badge">
      <defs>
        <radialGradient id="portrait-fill" cx="50%" cy="45%" r="60%">
          <stop offset="0%" stop-color="#e9e6e2"/>
          <stop offset="100%" stop-color="#c9ccd0"/>
        </radialGradient>
        <path id="ring-top" d="M 30 125 A 95 95 0 0 1 220 125"/>
        <path id="ring-bottom" d="M 22 125 A 103 103 0 0 0 228 125"/>
      </defs>
      <circle cx="125" cy="125" r="122" fill="var(--badge-green)"/>
      <circle cx="125" cy="125" r="119" fill="none" stroke="#ffffff" stroke-width="1.5"/>
      <circle cx="125" cy="125" r="84" fill="#ffffff"/>
      <circle cx="125" cy="125" r="76" fill="url(#portrait-fill)" role="img" aria-label="Portrait photo of a doctor in a white coat"/>
      <text font-family="Open Sans, sans-serif" font-size="17" fill="#ffffff">
        <textPath href="#ring-top" startOffset="50%" text-anchor="middle">Organic  •  Ecofriendly</textPath>
      </text>
      <text font-family="Open Sans, sans-serif" font-size="17" fill="#ffffff">
        <textPath href="#ring-bottom" startOffset="50%" text-anchor="middle">Sustainable  •  Healthy  •  Fair trading</textPath>
      </text>
      <text x="150" y="190" font-family="Open Sans, sans-serif" font-size="7" fill="#333333" transform="rotate(-30 150 190)">www.drvelmo.com</text>
    </svg>

    <p class="volume"><strong>300</strong>mL</p>
  </main>
</body>
</html>
```